Calder Vossik - Cinematographer

NEED:
I'm looking for a sleek, professional, modern business card that will give give the recipient the impression that they can trust their production will go smoothly by hiring me. I will bring creativity and knowledge to their shoot, so that we can create powerful images.
I am looking for a card with a strong style and design ethos that could be expanded to a website and a full visual/graphic/design entity for me.
ABOUT ME:
I am a mid-twenties cinematographer, I work on music video, narrative short, commercial, and corporate projects. I blend the science and artistry of cameras and filmmaking to tell a story. I'm an artist, a technician, and a manager.
DESIGN:
I like sleek, simple design. Black, dark grays, white, dark navy, steel blues, I love cyan, but also cyan and red. I am not a fan of earthy tones. I generally prefer modern, san-serif fonts over serifs. My old logo was based on an aperture, a multi-blade device at the back of a lens that controls how much light passes through, but I made it with so many colors, that it doesn't necessarily lend itself to a specific color-scheme or design ethos. I liked that the aperture design provided a sense of the technical requirements of my job. I'm a fan of matte business cards, but am open to plenty of specialty print processes to make an outstanding card.
ATTACHED FILES:
My Old Rainbox Aperture Logo, plus a few designs I've tried playing around with, but am not tied to. I AM OPEN TO NEW DESIGNS, DO NOT FEEL TIED TO THIS.
**I've pulled my old logo down from the attached files, and instead attached other business cards I like, so as not to mislead you where I would like to go.
INFO:
Name: Calder Vossik
Job: Cinematographer
Email: ccvossik@lumenpost.net
Phone: 415.555.0193
Website: caldervossik.com
Updates
I'm adding some images of other cards that I like, and removing my old logo, since I'm looking for something new, and don't want that old logo to push anyone a certain direction.

```html
<!DOCTYPE html>
<html lang="en">
<head>
<meta charset="utf-8">
<title>Calder Vossik – Cinematographer Business Card</title>
<link href="https://fonts.googleapis.com/css2?family=Lato:wght@400;700&display=swap" rel="stylesheet">
<style>
  :root {
    --backdrop: #3b3b3d;
    --card: #e6e6e6;
    --ink: #0b0b0b;
    --card-shadow: rgba(0, 0, 0, 0.35);
  }
  * { margin: 0; padding: 0; box-sizing: border-box; }
  html, body {
    width: 1200px;
    height: 926px;
    overflow: hidden;
    background: var(--backdrop);
    font-family: "Lato", sans-serif;
  }
  .card {
    position: absolute;
    left: 280px;
    width: 640px;
    height: 366px;
    background: var(--card);
    box-shadow: 0 8px 24px var(--card-shadow);
  }
  .card--front { top: 70px; }
  .card--back { top: 490px; }

  /* Front: plain name lockup */
  .front-name {
    position: absolute;
    inset: 0;
    display: flex;
    align-items: center;
    justify-content: center;
    gap: 18px;
    color: var(--ink);
  }
  .front-name__square {
    width: 34px;
    height: 34px;
    background: var(--ink);
  }
  .front-name__text {
    font-size: 34px;
    font-weight: 700;
    letter-spacing: 4px;
    text-transform: uppercase;
  }

  /* Back: contact side */
  .frame-strip {
    position: absolute;
    left: 20px;
    top: 20px;
    display: grid;
    grid-template-columns: repeat(2, 60px);
    grid-template-rows: repeat(5, 60px);
    gap: 6px;
  }
  .frame-strip__cell { background: var(--ink); }
  .website {
    position: absolute;
    left: 158px;
    top: 22px;
    writing-mode: vertical-rl;
    font-size: 13px;
    letter-spacing: 1px;
    color: var(--ink);
  }
  .identity {
    position: absolute;
    right: 30px;
    top: 40px;
    text-align: right;
    color: var(--ink);
  }
  .identity__name {
    font-size: 26px;
    font-weight: 700;
    letter-spacing: 2px;
    text-transform: uppercase;
  }
  .identity__role {
    font-size: 15px;
    letter-spacing: 1.5px;
    text-transform: uppercase;
    margin-top: 2px;
  }
  .contact {
    position: absolute;
    right: 30px;
    bottom: 30px;
    text-align: right;
    font-size: 17px;
    line-height: 1.4;
    letter-spacing: 0.5px;
    color: var(--ink);
  }
  .contact__label { font-weight: 700; }
</style>
</head>
<body>
  <section class="card card--front" aria-label="Card front">
    <div class="front-name">
      <span class="front-name__square" aria-hidden="true"></span>
      <span class="front-name__text">Calder Vossik</span>
    </div>
  </section>

  <section class="card card--back" aria-label="Card back">
    <div class="frame-strip">
      <div class="frame-strip__cell"></div><div class="frame-strip__cell"></div>
      <div class="frame-strip__cell"></div><div class="frame-strip__cell"></div>
      <div class="frame-strip__cell"></div><div class="frame-strip__cell"></div>
      <div class="frame-strip__cell"></div><div class="frame-strip__cell"></div>
      <div class="frame-strip__cell"></div><div class="frame-strip__cell"></div>
    </div>
    <div class="website">www.caldervossik.com</div>
    <div class="identity">
      <h1 class="identity__name">Calder Vossik</h1>
      <p class="identity__role">Cinematographer</p>
    </div>
    <div class="contact">
      <p><span class="contact__label">phone</span>: 415.555.0193</p>
      <p><span class="contact__label">email</span>: ccvossik@lumenpost.net</p>
    </div>
  </section>
</body>
</html>
```